Tidy paddock Services

After a high quality design website. we are a company that provides services to people that own land and need a hand getting on top of the delayed jobs.
would want a number of tab/ pages for the web page.
Home page / About us page / services page / Gallery page. / Contact us page
we offer a wide range of services .listed below

Stock Work (title)

Stock movement
Break feeding
Temporary staffing

Spraying (title)

Spraying weeds
Spraying gorse

Pastures (title)

Fertilizing
Topping

Building (title)

Habitable sheds
Farm sheds
Sheep yards
Cattle yards
Repair farm buildings
Decks
Retaining walls

Fencing (title)

Stock fencing
Post & rail
Stock yards repair
Electric fencing install & repairs

Water Management (title)

Water trough installation
Water scheme install
Water trough cleaning
Farm water maintenance
Water ponds
Ornamental ponds
Drainage

General (title)

Lawn mowing
Hedge trimming
Pruning trees
Metaling drive ways & races
Water blasting
Small digger work
Little tip truck cartage
Home kill management
Mulching gorse
Section clearing

```html
<!DOCTYPE html>
<html lang="en">
<head>
<meta charset="utf-8">
<title>Tidy paddock Services</title>
<link rel="stylesheet" href="https://fonts.googleapis.com/css2?family=Poppins:wght@400;500;600;700;800&display=swap">
<style>
:root{
  --green:#5f9f1c;
  --green-dark:#4b8510;
  --green-soft:#eef5e4;
  --ink:#1c1c1c;
  --muted:#5a5a5a;
  --light:#f3f3f1;
  --line:#dcdcdc;
  --dark:#101110;
  --star:#f08a24;
}
*{box-sizing:border-box;margin:0;padding:0}
html,body{width:1200px;height:5338px;overflow:hidden}
body{position:relative;background:#fff;font-family:"Poppins",sans-serif;color:var(--ink)}
.abs{position:absolute}
a{color:inherit;text-decoration:none}

/* header */
.site-header{position:absolute;left:0;top:0;width:1200px;height:68px;background:#fff;z-index:5}
.brand{position:absolute;display:flex;align-items:center;gap:8px;font-weight:700;font-size:15px;color:var(--green);text-transform:uppercase;line-height:1}
.brand-dot{width:26px;height:26px;border:2px solid var(--green);border-radius:50%}
.site-header .brand{left:77px;top:22px}
.main-nav{position:absolute;top:0;left:378px;height:68px;display:flex;gap:0}
.main-nav a{position:absolute;top:25px;font-size:12px;font-weight:600;text-transform:uppercase;white-space:nowrap}
.main-nav a.active{color:var(--green)}
.main-nav a.active::after{content:"";position:absolute;left:0;right:0;top:41px;height:3px;background:var(--green)}
.header-call{position:absolute;left:933px;top:22px;display:flex;align-items:center;gap:10px;font-size:13px;font-weight:500;color:var(--green)}
.header-call .ico{width:24px;height:24px;border-radius:50%;background:#111;display:flex;align-items:center;justify-content:center}

/* hero */
.hero{position:absolute;left:0;top:68px;width:1200px;height:668px;overflow:hidden}
.hero-photo{position:absolute;inset:0;background:linear-gradient(90deg,rgba(20,24,20,.78) 0%,rgba(20,24,20,.45) 30%,rgba(0,0,0,0) 55%),linear-gradient(120deg,#4a4d45 0%,#8c8a7a 35%,#c9c4a8 55%,#b6a040 70%,#d27a2c 85%,#6f5a3a 100%)}
.hero-curve{position:absolute;left:0;bottom:0}
.hero-kicker{position:absolute;left:83px;top:148px;font-size:27px;font-weight:500;color:var(--green);text-transform:uppercase}
.hero-title{position:absolute;left:83px;top:180px;font-size:50px;line-height:56px;font-weight:700;color:#fff;text-transform:uppercase}
.hero-text{position:absolute;left:83px;top:300px;width:300px;font-size:13.5px;line-height:21px;color:#fff}
.btn{display:inline-flex;align-items:center;justify-content:center;font-weight:600;text-transform:uppercase;font-size:11px}
.btn-green{background:var(--green);color:#fff}
.hero .btn{position:absolute;left:83px;top:407px;width:120px;height:31px;font-size:10px}
.scroll-cue{position:absolute;left:1148px;top:240px;width:20px;height:170px}
.scroll-cue span{position:absolute;left:4px;top:125px;transform:rotate(90deg);transform-origin:left top;font-size:9px;color:#fff;white-space:nowrap;letter-spacing:1px;left:14px;top:68px}
.scroll-cue i{position:absolute;left:9px;top:0;width:1px;height:60px;background:#fff}

/* section titles */
.section-title{position:absolute;font-size:34px;font-weight:700;text-transform:uppercase;line-height:1;white-space:nowrap}
.section-title em{font-style:normal;color:var(--green)}

/* services */
.services{position:absolute;left:0;top:736px;width:1200px;height:1175px;background:linear-gradient(180deg,#f3f3f1 0%,#f6f6f4 60%,#eeeeec 100%)}
.services .section-title{left:0;width:1200px;text-align:center;top:102px}
.services .lead{position:absolute;left:260px;width:680px;top:158px;text-align:center;font-size:12.5px;line-height:21px;color:var(--muted)}
.svc-card{position:absolute;width:296px;background:#fff;box-shadow:0 4px 18px rgba(0,0,0,.08)}
.svc-photo{height:185px;clip-path:polygon(0 0,100% 0,100% 62%,50% 100%,0 62%)}
.svc-icon{position:absolute;left:112px;top:178px;width:72px;height:72px;border-radius:50%;background:var(--green);border:4px solid #fff;box-shadow:0 0 0 2px var(--green)}
.svc-name{position:absolute;left:0;width:100%;top:265px;text-align:center;font-size:13px;font-weight:600;text-transform:uppercase}
.svc-card.featured{background:var(--green);color:#fff}
.svc-card.featured .svc-icon{background:#1a1a1a;box-shadow:0 0 0 2px #fff}
.svc-desc{position:absolute;left:38px;width:220px;top:292px;text-align:center;font-size:10.5px;line-height:17px}
.svc-more{position:absolute;left:0;width:100%;top:390px;text-align:center;font-size:9.5px;font-weight:700;text-decoration:underline}
.btn-outline{position:absolute;border:2px solid var(--green);background:#fff;color:var(--ink)}

/* about */
.about{position:absolute;left:0;top:1911px;width:1200px;height:836px;background:linear-gradient(135deg,#fff 30%,#f1f6ea 100%)}
.about-photo{position:absolute;left:129px;top:87px;width:659px;height:651px;border-radius:18px;background:linear-gradient(135deg,#c9d2d6 0%,#9fb0bb 40%,#6f86a6 70%,#d7d9d6 100%)}
.about-card{position:absolute;left:537px;top:156px;width:533px;height:516px;background:#fff;border-radius:10px;box-shadow:0 8px 30px rgba(0,0,0,.10);padding:20px}
.about-frame{position:absolute;left:20px;top:20px;right:20px;bottom:20px;border:1px solid var(--green);border-radius:12px;border-right-color:transparent}
.about-card .section-title{position:absolute;left:66px;top:74px;font-size:34px;line-height:42px}
.about-text{position:absolute;left:66px;top:160px;width:410px;font-size:13.5px;line-height:22.5px;color:var(--muted)}
.about-card .btn{position:absolute;left:66px;top:421px;width:143px;height:35px}

/* gallery */
.gallery{position:absolute;left:0;top:2747px;width:1200px;height:545px}
.g-cell{position:absolute;width:400px;height:272px}
.g-intro{background:var(--light)}
.g-intro .section-title{left:70px;top:56px;font-size:32px;line-height:40px}
.g-intro p{position:absolute;left:75px;top:150px;width:260px;font-size:12.5px;line-height:21px;color:var(--muted)}

/* testimonials */
.testimonials{position:absolute;left:0;top:3292px;width:1200px;height:538px;background:linear-gradient(180deg,#fff 0%,#f4f4f2 100%);overflow:hidden}
.testimonials .section-title{left:129px;top:90px}
.arrow{position:absolute;top:89px;width:30px;height:30px;border-radius:50%;display:flex;align-items:center;justify-content:center}
.t-card{position:absolute;top:174px;width:449px;height:342px;background:#fff;box-shadow:0 4px 18px rgba(0,0,0,.07);text-align:center}
.t-quote{position:absolute;left:195px;top:40px;width:46px;height:46px;border:3px solid var(--green);border-radius:50%;color:var(--green);font-size:40px;font-weight:700;line-height:58px}
.t-name{position:absolute;left:0;width:100%;top:110px;font-size:14px;color:var(--green)}
.t-text{position:absolute;left:45px;right:45px;top:145px;font-size:12px;line-height:22px;color:var(--muted)}
.t-stars{position:absolute;left:0;width:100%;top:280px;font-size:14px;color:var(--star);letter-spacing:1px}

/* news */
.news{position:absolute;left:0;top:3830px;width:1200px;height:710px;background:#fff}
.news .section-title{left:0;width:1200px;text-align:center;top:80px}
.n-card{position:absolute;top:150px;width:290px;height:373px;background:#fff;box-shadow:0 4px 18px rgba(0,0,0,.08)}
.n-photo{height:214px;border-radius:14px 14px 0 0}
.n-date{position:absolute;left:26px;top:240px;border:1px solid var(--green);border-radius:2px;padding:1px 6px;font-size:9px;color:var(--green)}
.n-title{position:absolute;left:26px;top:262px;width:240px;font-size:12.5px;line-height:18px;font-weight:700;text-transform:uppercase}
.n-more{position:absolute;left:26px;top:332px;display:flex;align-items:center;gap:10px;font-size:9.5px;font-weight:700;color:var(--green)}
.n-more i{width:18px;height:18px;border-radius:50%;background:var(--green);display:flex;align-items:center;justify-content:center}
.btn-dark-outline{position:absolute;left:483px;top:575px;width:234px;height:42px;border:2px solid #111;background:#fff;font-size:11px}

/* footer */
.site-footer{position:absolute;left:0;top:4530px;width:1200px;height:808px;background:var(--dark);overflow:hidden}
.footer-curve{position:absolute;left:0;top:0}
.contact-box{position:absolute;left:166px;top:132px;width:352px;height:390px;background:var(--green);color:#fff}
.contact-box h2{position:absolute;left:35px;top:46px;font-size:31px;font-weight:700;text-transform:uppercase}
.contact-box .intro{position:absolute;left:35px;top:98px;width:270px;font-size:12px;line-height:19px}
.c-item{position:absolute;left:35px;display:flex;gap:14px;font-size:10px;line-height:14px}
.c-item .ring{flex:none;width:28px;height:28px;border:2px solid #fff;border-radius:50%;display:flex;align-items:center;justify-content:center}
.form-field{position:absolute;height:58px;border-bottom:1px solid #777}
.form-field .f-ico{position:absolute;left:0;top:8px;width:16px;height:16px;border-radius:50%;background:var(--green);display:flex;align-items:center;justify-content:center}
.form-field b{position:absolute;left:30px;top:2px;font-size:11px;font-weight:500;color:#fff}
.form-field span{position:absolute;left:30px;top:20px;font-size:9.5px;color:#9a9a9a}
.submit{position:absolute;left:572px;top:476px;width:129px;height:36px;background:var(--green);color:#fff;font-size:11px}
.site-footer .brand{left:140px;top:620px;color:var(--green)}
.f-col-title{position:absolute;font-size:10.5px;font-weight:700;color:#fff;text-transform:uppercase}
.f-links{position:absolute;left:473px;top:638px;font-size:12px;color:#fff;white-space:nowrap}
.social{position:absolute;left:940px;top:636px;display:flex;gap:14px}
.social i{width:24px;height:24px;border:1.5px solid #fff;border-radius:50%;display:block}
.f-rule{position:absolute;left:0;top:715px;width:1200px;height:1px;background:#2c2c2c}
.copy{position:absolute;top:745px;font-size:12px;color:#fff}
</style>
</head>
<body>

<header class="site-header">
  <a class="brand" href="#"><span class="brand-dot"></span>Tidy paddock Services</a>
  <nav class="main-nav">
    <a class="active" href="#" style="left:20px">Home</a>
    <a href="#" style="left:115px">About Us</a>
    <a href="#" style="left:193px">Our Services</a>
    <a href="#" style="left:330px">Gallery</a>
    <a href="#" style="left:430px">Contact Us</a>
  </nav>
  <div class="header-call">
    <span class="ico"><svg width="12" height="12" viewBox="0 0 24 24"><path fill="#fff" d="M6.6 10.8a15 15 0 0 0 6.6 6.6l2.2-2.2c.3-.3.7-.4 1-.2 1.1.4 2.3.6 3.6.6.6 0 1 .4 1 1V20c0 .6-.4 1-1 1A17 17 0 0 1 3 4c0-.6.4-1 1-1h3.5c.6 0 1 .4 1 1 0 1.3.2 2.5.6 3.6.1.3 0 .7-.2 1z"/></svg></span>
    Call +1 555 0147 382
  </div>
</header>

<section class="hero">
  <div class="hero-photo" role="img" aria-label="Photo of smiling workers in hard hats and safety vests"></div>
  <svg class="hero-curve" width="1200" height="190" viewBox="0 0 1200 190" aria-hidden="true">
    <path d="M0 80 Q560 190 1200 40 L1200 190 L0 190Z" fill="#f3f3f1"/>
    <path d="M300 150 Q760 160 1200 36" fill="none" stroke="#5f9f1c" stroke-width="8"/>
  </svg>
  <p class="hero-kicker">Welcome to</p>
  <h1 class="hero-title">Tidy paddock<br>Services</h1>
  <p class="hero-text">Sed ut perspiciatis unde omnis iste natus error sit voluptatem accusantium doloremque laudantium, totam rem aperiam, eaque ipsa quae ab illo</p>
  <a class="btn btn-green" href="#">Get Started</a>
  <div class="scroll-cue"><i></i><span>SCROLL DOWN</span>
    <svg class="abs" style="left:3px;top:150px" width="14" height="10" viewBox="0 0 14 10"><path d="M1 1l6 6 6-6" fill="none" stroke="#fff" stroke-width="1.5"/></svg>
  </div>
</section>

<section class="services">
  <h2 class="section-title"><em>Our</em> Services</h2>
  <p class="lead">Sed ut perspiciatis unde omnis iste natus error sit voluptatem accusantium doloremque laudantium, totam rem aperiam, eaque ipsa quae ab illo inventore veritatis et quasi architecto</p>

  <article class="svc-card" style="left:129px;top:247px;height:302px">
    <div class="svc-photo" role="img" aria-label="Photo of a woman with a tablet among green plants" style="background:linear-gradient(135deg,#8fb84a,#3f6b22 60%,#c7d9a0)"></div>
    <span class="svc-icon"></span><h3 class="svc-name">Stock Work</h3>
  </article>
  <article class="svc-card featured" style="left:452px;top:247px;height:431px">
    <div class="svc-photo" role="img" aria-label="Photo of a worker spraying weeds on grass" style="background:linear-gradient(135deg,#2e3a26,#6f9a3a 60%,#a8c86a)"></div>
    <span class="svc-icon"></span><h3 class="svc-name">Spraying</h3>
    <p class="svc-desc">Sed ut perspiciatis unde omnis iste natus error sit voluptatem accusantium doloremque laudantium, totam rem aperiam, eaque ipsa quae ab illo inventore veritatis et quasi architecto</p>
    <a class="svc-more" href="#">READ MORE</a>
  </article>
  <article class="svc-card" style="left:773px;top:247px;height:302px">
    <div class="svc-photo" role="img" aria-label="Photo of cattle grazing on a green pasture" style="background:linear-gradient(180deg,#b9cfa0 0%,#7ea34a 45%,#5d8a2c 100%)"></div>
    <span class="svc-icon"></span><h3 class="svc-name">Pastures</h3>
  </article>
  <article class="svc-card" style="left:129px;top:574px;height:305px">
    <div class="svc-photo" role="img" aria-label="Photo of a white farm barn in green fields" style="background:linear-gradient(180deg,#a9c2d8 0%,#d9a35a 35%,#e8ecef 55%,#6d9a34 75%)"></div>
    <span class="svc-icon"></span><h3 class="svc-name">Building</h3>
  </article>
  <article class="svc-card" style="left:452px;top:698px;height:303px">
    <div class="svc-photo" role="img" aria-label="Photo of a new timber fence" style="background:linear-gradient(180deg,#b9c6cc 0%,#b27a44 40%,#8a5a30 100%)"></div>
    <span class="svc-icon"></span><h3 class="svc-name">Fencing</h3>
  </article>
  <article class="svc-card" style="left:773px;top:574px;height:305px">
    <div class="svc-photo" role="img" aria-label="Photo of a person mowing a lawn" style="background:linear-gradient(135deg,#4d6b2a,#7fae3c 50%,#3a3a2c)"></div>
    <span class="svc-icon"></span><h3 class="svc-name">General</h3>
  </article>

  <a class="btn btn-outline" href="#" style="left:481px;top:1055px;width:236px;height:44px">See All Our Services</a>
</section>

<section class="about">
  <div class="about-photo" role="img" aria-label="Photo of two smiling men in business clothes"></div>
  <div class="about-card">
    <div class="about-frame"></div>
    <h2 class="section-title"><em>About</em> Tidy paddock<br>Services</h2>
    <p class="about-text">Sed ut perspiciatis unde omnis iste natus error sit voluptatem accusantium doloremque laudantium, totam rem aperiam, eaque ipsa quae ab illo inventore veritatis et quasi architecto beatae vitae dicta sunt explicabo. Nemo enim ipsam voluptatem quia voluptas sit aspernatur aut odit aut fugit, sed quia consequuntur magni dolores eos qui ratione voluptatem sequi nesciunt. Neque porro quisquam est, qui dolorem ipsum quia dolor sit amet, consectetur, adipisci velit, sed quia non numquam eius modi tempora incidunt ut labore et dolore magnam aliquam quaerat voluptatem.</p>
    <a class="btn btn-green" href="#">Learn More</a>
  </div>
</section>

<section class="gallery">
  <div class="g-cell g-intro" style="left:0;top:0">
    <h2 class="section-title"><em>Our</em><br>Gallery</h2>
    <p>Sed ut perspiciatis unde omnis iste natus error sit voluptatem ccusantium doloremque laudantium, totam rem aperiam, eaque ipsa quae ab illo</p>
  </div>
  <div class="g-cell" style="left:400px;top:0;background:linear-gradient(160deg,#d8e4e8,#3aa6d6 45%,#1a74b8)" role="img" aria-label="Photo of a swimming pool with a steel ladder"></div>
  <div class="g-cell" style="left:800px;top:0;background:linear-gradient(135deg,#6b8fb0,#a5532e 40%,#7e3a22 80%,#5d8a2c)" role="img" aria-label="Photo of a red timber fence beside a house"></div>
  <div class="g-cell" style="left:0;top:272px;background:linear-gradient(135deg,#5c7f2c,#2c2f2a 45%,#a0a6a2 60%,#6f9a34)" role="img" aria-label="Photo of a worker using a backpack sprayer on grass"></div>
  <div class="g-cell" style="left:400px;top:272px;background:linear-gradient(180deg,#b4b7a8 0%,#7d8f4a 40%,#5d7a2c 100%)" role="img" aria-label="Photo of a wire fence with a red farm building behind"></div>
  <div class="g-cell" style="left:800px;top:272px;background:linear-gradient(135deg,#6d5a48,#c8b88c 40%,#d0762c 65%,#3a3028)" role="img" aria-label="Photo of builders in hard hats working at a table"></div>
</section>

<section class="testimonials">
  <h2 class="section-title"><em>Customer</em> Testimonials</h2>
  <span class="arrow" style="left:997px;background:var(--green)"><svg width="14" height="12" viewBox="0 0 14 12"><path d="M13 6H2M6 1 1 6l5 5" fill="none" stroke="#fff" stroke-width="1.6"/></svg></span>
  <span class="arrow" style="left:1039px;background:#1a1a1a"><svg width="14" height="12" viewBox="0 0 14 12"><path d="M1 6h11M8 1l5 5-5 5" fill="none" stroke="#fff" stroke-width="1.6"/></svg></span>

  <article class="t-card" style="left:129px">
    <span class="t-quote">“</span><p class="t-name">- Mara Quill</p>
    <p class="t-text">Lorem ipsum dolor sit amet, consectetur adipiscing elit, sed do eiusmod tempor incididunt ut labore et dolore magna aliqua. Ut enim ad minim veniam, quis nostrud exercitation ullamco laboris nisi ut aliquip ex ea commodo consequat. Duis aute irure dolor in reprehenderit in voluptate velit esse cillum dolore eu fugiat</p>
    <p class="t-stars">★★★★★</p>
  </article>
  <article class="t-card" style="left:591px">
    <span class="t-quote">“</span><p class="t-name">- Mara Quill</p>
    <p class="t-text">Lorem ipsum dolor sit amet, consectetur adipiscing elit, sed do eiusmod tempor incididunt ut labore et dolore magna aliqua. Ut enim ad minim veniam, quis nostrud exercitation ullamco laboris nisi ut aliquip ex ea commodo consequat. Duis aute irure dolor in reprehenderit in voluptate velit esse cillum dolore eu fugiat</p>
    <p class="t-stars">★★★★★</p>
  </article>
  <article class="t-card" style="left:1053px">
    <span class="t-quote">“</span><p class="t-name">- Mara Quill</p>
    <p class="t-text">Lorem ipsum dolor sit amet, consectetur adipiscing elit, sed do eiusmod tempor incididunt ut labore et dolore magna aliqua. Ut enim ad minim veniam, quis nostrud exercitation ullamco laboris nisi ut aliquip ex ea commodo consequat. Duis aute irure dolor in reprehenderit in voluptate velit esse cillum dolore eu fugiat</p>
    <p class="t-stars">★★★★★</p>
  </article>
</section>

<section class="news">
  <h2 class="section-title"><em>Latest</em> News</h2>
  <article class="n-card" style="left:129px">
    <div class="n-photo" role="img" aria-label="Photo of a team meeting at a wall of sticky notes" style="background:linear-gradient(135deg,#e9b97a,#f1efe8 40%,#8fb0c8 70%,#d8d4cc)"></div>
    <span class="n-date">June 07 2024</span>
    <h3 class="n-title">Excepteur sint occaecat cupidatat non proident, sunt in culpa qui</h3>
    <a class="n-more" href="#">READ MORE <i><svg width="9" height="8" viewBox="0 0 9 8"><path d="M0 4h7M4 1l3 3-3 3" fill="none" stroke="#fff" stroke-width="1.3"/></svg></i></a>
  </article>
  <article class="n-card" style="left:456px">
    <div class="n-photo" role="img" aria-label="Photo of a hand holding a garden pressure sprayer" style="background:linear-gradient(135deg,#2e4a1c,#5f8a2c 40%,#f2f2ee 60%,#d8872a)"></div>
    <span class="n-date">June 07 2024</span>
    <h3 class="n-title">Excepteur sint occaecat cupidatat non proident, sunt in culpa qui</h3>
    <a class="n-more" href="#">READ MORE <i><svg width="9" height="8" viewBox="0 0 9 8"><path d="M0 4h7M4 1l3 3-3 3" fill="none" stroke="#fff" stroke-width="1.3"/></svg></i></a>
  </article>
  <article class="n-card" style="left:781px">
    <div class="n-photo" role="img" aria-label="Photo of brown cattle grazing at sunset" style="background:linear-gradient(180deg,#d9c7a0 0%,#8a5a32 45%,#6d8a34 100%)"></div>
    <span class="n-date">June 07 2024</span>
    <h3 class="n-title">Excepteur sint occaecat cupidatat non proident, sunt in culpa qui</h3>
    <a class="n-more" href="#">READ MORE <i><svg width="9" height="8" viewBox="0 0 9 8"><path d="M0 4h7M4 1l3 3-3 3" fill="none" stroke="#fff" stroke-width="1.3"/></svg></i></a>
  </article>
  <a class="btn btn-dark-outline" href="#">View More Latest Blog</a>
</section>

<footer class="site-footer">
  <svg class="footer-curve" width="1200" height="110" viewBox="0 0 1200 110" aria-hidden="true">
    <path d="M0 0H1200V110H0Z" fill="#fff"/>
    <path d="M0 110 Q600 -10 1200 110Z" fill="#5f9f1c"/>
    <path d="M0 110 Q600 12 1200 110Z" fill="#101110"/>
  </svg>

  <div class="contact-box">
    <h2>Contact Us</h2>
    <p class="intro">Excepteur sint occaecat cupidatat non proident, sunt in culpa qui officia</p>
    <div class="c-item" style="top:160px">
      <span class="ring"><svg width="12" height="14" viewBox="0 0 12 14"><path d="M6 1a4.5 4.5 0 0 0-4.5 4.5C1.5 9 6 13 6 13s4.5-4 4.5-7.5A4.5 4.5 0 0 0 6 1z" fill="none" stroke="#fff" stroke-width="1.4"/><circle cx="6" cy="5.5" r="1.5" fill="#fff"/></svg></span>
      <p>Tidy paddock Services<br>PO Box 4821 Excepteur sint<br>occaecat cupidatat</p>
    </div>
    <div class="c-item" style="top:238px">
      <span class="ring"><svg width="12" height="12" viewBox="0 0 24 24"><path fill="#fff" d="M6.6 10.8a15 15 0 0 0 6.6 6.6l2.2-2.2c.3-.3.7-.4 1-.2 1.1.4 2.3.6 3.6.6.6 0 1 .4 1 1V20c0 .6-.4 1-1 1A17 17 0 0 1 3 4c0-.6.4-1 1-1h3.5c.6 0 1 .4 1 1 0 1.3.2 2.5.6 3.6.1.3 0 .7-.2 1z"/></svg></span>
      <p>Phone<br>+1 555 0147 382</p>
    </div>
    <div class="c-item" style="top:302px">
      <span class="ring"><svg width="13" height="10" viewBox="0 0 13 10"><rect x=".7" y=".7" width="11.6" height="8.6" fill="none" stroke="#fff" stroke-width="1.3"/><path d="M1 1l5.5 4.5L12 1" fill="none" stroke="#fff" stroke-width="1.3"/></svg></span>
      <p>Email<br>hello@tidypaddock.example</p>
    </div>
  </div>

  <form>
    <div class="form-field" style="left:572px;top:142px;width:234px"><span class="f-ico"></span><b>Name</b><span>First Name</span></div>
    <div class="form-field" style="left:836px;top:142px;width:234px"><span class="f-ico"></span><b>Name</b><span>Last Name</span></div>
    <div class="form-field" style="left:572px;top:218px;width:234px"><span class="f-ico"></span><b>Email Address</b><span>name@example.com</span></div>
    <div class="form-field" style="left:836px;top:218px;width:234px"><span class="f-ico"></span><b>Phone</b><span>000 000 0000</span></div>
    <div class="form-field" style="left:572px;top:294px;width:498px"><span class="f-ico"></span><b>Tidy paddock Services</b><span>Excepteur sint occaecat cupidatat</span></div>
    <div class="form-field" style="left:572px;top:370px;width:498px;height:76px"><span class="f-ico"></span><b>Message</b><span>Excepteur sint occaecat cupidatat</span></div>
    <button class="btn submit" type="button" style="border:0;font-family:inherit">Submit</button>
  </form>

  <a class="brand" href="#"><span class="brand-dot"></span>Tidy paddock Services</a>
  <p class="f-col-title" style="left:473px;top:612px">Quick Links</p>
  <p class="f-links">Home &nbsp;|&nbsp; About &nbsp;|&nbsp; Services &nbsp;|&nbsp; Gallery &nbsp;|&nbsp; Contact</p>
  <p class="f-col-title" style="left:935px;top:605px;font-size:12px;font-weight:500;text-transform:none">Follow Us</p>
  <div class="social"><i></i><i></i><i></i><i></i></div>
  <div class="f-rule"></div>
  <p class="copy" style="left:129px">Copyright © Tidy paddock Services 2024. All rights reserved.</p>
  <p class="copy" style="right:130px">Privacy | Terms of Use | Sitemap</p>
</footer>

</body>
</html>
```